A restaurant needs a new design for menu and presentation flyers.

The name of the restaurant located in Germany is ,, GASTSTÄTTE AM BACH" . It means RESTAURANT THE BROOK. I attached two photos for reference to see the actual fonts.
I would like to have something close to the fonts we have now. I would like to add a crown representation.Any idea is welcomed.

Target Market(s)

GERMANY

Contact Information for Business Card

Must have AM BACH logo.

Requirements
Nice to have
• A crown representation or other symbol who can be representative for our business.
An font close to actual fonts.

```html
<!DOCTYPE html>
<html lang="de">
<head>
<meta charset="utf-8">
<title>Gaststätte am Bach – Menu</title>
<link href="https://fonts.googleapis.com/css2?family=Barlow+Condensed:wght@400;600&family=Barlow:wght@400;500;600&family=Pinyon+Script&family=Figtree:wght@400&family=Cinzel:wght@500&display=swap" rel="stylesheet">
<style>
  :root {
    --ink-dark: #1c1c1c;
    --panel-dark: #161616;
    --cream: #fdefdc;
    --gold: #c8862f;
    --gold-light: #e2b35e;
    --text: #2a2522;
    --muted: #6b6460;
  }
  * { margin: 0; padding: 0; box-sizing: border-box; }
  html, body { width: 1200px; height: 856px; overflow: hidden; }
  body { position: relative; background: var(--cream); font-family: "Barlow", sans-serif; }

  .brand-panel {
    position: absolute; left: 0; top: 0; width: 404px; height: 856px;
    background: radial-gradient(circle at 40% 40%, #242424 0%, var(--panel-dark) 75%);
  }
  .brand-name {
    position: absolute; left: 0; width: 404px; top: 290px; text-align: center;
    font-family: "Cinzel", serif; font-weight: 500; color: var(--gold-light);
  }
  .brand-name .main { display: block; font-size: 46px; letter-spacing: 3px; line-height: 1.1; }
  .brand-name .sub { display: block; font-size: 13px; letter-spacing: 6px; margin-top: 8px; }
  .divider { position: absolute; top: 654px; left: 129px; width: 158px; height: 1px; }
  .contacts {
    position: absolute; left: 0; width: 404px; top: 694px; text-align: center;
    font-family: "Barlow Condensed", sans-serif; font-size: 16px; color: var(--gold-light);
  }
  .contacts li { list-style: none; height: 29px; display: flex; justify-content: center; align-items: center; gap: 7px; }
  .contacts svg { width: 13px; height: 13px; flex: none; }
  .social-dot { width: 12px; height: 12px; border-radius: 50%; background: #fff; flex: none; }

  .menu-title {
    position: absolute; left: 404px; width: 796px; top: 48px; text-align: center;
    font-family: "Pinyon Script", cursive; font-size: 60px; color: var(--gold); line-height: 1;
  }
  .menu-title .dot { font-family: "Barlow", sans-serif; font-size: 16px; vertical-align: 24px; margin: 0 22px; }

  .ribbon {
    position: absolute; height: 40px; background: var(--gold); color: #fff;
    font-family: "Barlow Condensed", sans-serif; font-weight: 600; font-size: 20px;
    display: flex; align-items: center; padding-left: 17px;
  }
  .ribbon.tail { width: 140px; clip-path: polygon(0 0, 100% 0, 96% 50%, 100% 100%, 0 100%); }
  .ribbon.both { width: 224px; justify-content: center; padding: 0;
    clip-path: polygon(0 0, 100% 0, 98% 50%, 100% 100%, 0 100%, 2% 50%); }

  .column-rule { position: absolute; left: 795px; top: 225px; width: 1.5px; height: 365px; background: var(--gold); }

  .dish { position: absolute; width: 300px; }
  .dish-name { font-family: "Figtree", sans-serif; font-size: 17.5px; color: var(--text); letter-spacing: .3px; line-height: 1; height: 24px; }
  .dish-name .initial { font-family: "Pinyon Script", cursive; font-size: 27px; vertical-align: -2px; }
  .dish-desc { margin-top: 3px; font-size: 11.6px; line-height: 15.5px; color: var(--muted); width: 248px; }
  .leader { display: inline-block; width: 66px; border-bottom: 1px dotted var(--muted); margin-left: 1px; }
  .price { position: absolute; left: 262px; top: 28px; color: var(--gold); font-weight: 600; font-size: 29px; line-height: 1; }
  .price sup { font-size: 15px; vertical-align: 12px; margin-right: 1px; }
</style>
</head>
<body>
  <aside class="brand-panel">
    <div class="brand-name"><span class="main">Am Bach</span><span class="sub">GASTSTÄTTE</span></div>
    <svg class="divider" viewBox="0 0 158 8" style="height:8px;top:650px">
      <line x1="0" y1="4" x2="70" y2="4" stroke="#6a6a6a" stroke-width="1"/>
      <rect x="76" y="1.5" width="5" height="5" transform="rotate(45 78.5 4)" fill="none" stroke="#8a8a8a"/>
      <line x1="88" y1="4" x2="158" y2="4" stroke="#6a6a6a" stroke-width="1"/>
    </svg>
    <ul class="contacts">
      <li><svg viewBox="0 0 12 16"><path d="M6 0a6 6 0 0 0-6 6c0 4.5 6 10 6 10s6-5.5 6-10a6 6 0 0 0-6-6zm0 8.5A2.5 2.5 0 1 1 6 3.5a2.5 2.5 0 0 1 0 5z" fill="#fff"/></svg>Mühlenweg 7, 34567 Talbach (Fulda)</li>
      <li><svg viewBox="0 0 16 16"><circle cx="8" cy="8" r="8" fill="#fff"/><path d="M5 4l1.6-.3 1 2.2-1 .8c.5 1.2 1.4 2.1 2.6 2.6l.8-1 2.2 1-.3 1.6c-3.5.2-6.9-3.3-6.9-6.9z" fill="#161616"/></svg>Frau Lena Brandt 170 12345678</li>
      <li><span class="social-dot"></span>/AmBachTalbach</li>
    </ul>
  </aside>

  <h1 class="menu-title"><span class="dot">•</span>Menu<span class="dot">•</span></h1>

  <div class="ribbon tail" style="left:455px;top:161px">MAIN DISHES</div>
  <div class="ribbon tail" style="left:853px;top:161px">SIDE DISHES</div>
  <div class="column-rule"></div>

  <!-- main dishes -->
  <div class="dish" style="left:455px;top:222px"><p class="dish-name"><span class="initial">S</span>INT OCCAECAT</p><p class="dish-desc">Sed ut perspiciatis unde omnis iste natus error sit voluptatem accusantium<span class="leader"></span></p><p class="price"><sup>€</sup>5</p></div>
  <div class="dish" style="left:455px;top:322px"><p class="dish-name"><span class="initial">Q</span>UIS NOSTRUD</p><p class="dish-desc">Sed ut perspiciatis unde omnis iste natus error sit voluptatem accusantium<span class="leader"></span></p><p class="price"><sup>€</sup>7</p></div>
  <div class="dish" style="left:455px;top:422px"><p class="dish-name"><span class="initial">E</span>USMOD TEMPOR</p><p class="dish-desc">Sed ut perspiciatis unde omnis iste natus error sit voluptatem accusantium<span class="leader"></span></p><p class="price"><sup>€</sup>8</p></div>
  <div class="dish" style="left:455px;top:522px"><p class="dish-name"><span class="initial">L</span>OREM IPSUM</p><p class="dish-desc">Sed ut perspiciatis unde omnis iste natus error sit voluptatem accusantium<span class="leader"></span></p><p class="price"><sup>€</sup>3</p></div>

  <!-- side dishes -->
  <div class="dish" style="left:853px;top:222px"><p class="dish-name"><span class="initial">S</span>INT OCCAECAT</p><p class="dish-desc">Sed ut perspiciatis unde omnis iste natus error sit voluptatem accusantium<span class="leader"></span></p><p class="price"><sup>€</sup>5</p></div>
  <div class="dish" style="left:853px;top:322px"><p class="dish-name"><span class="initial">Q</span>UIS NOSTRUD</p><p class="dish-desc">Sed ut perspiciatis unde omnis iste natus error sit voluptatem accusantium<span class="leader"></span></p><p class="price"><sup>€</sup>7</p></div>
  <div class="dish" style="left:853px;top:422px"><p class="dish-name"><span class="initial">E</span>USMOD TEMPOR</p><p class="dish-desc">Sed ut perspiciatis unde omnis iste natus error sit voluptatem accusantium<span class="leader"></span></p><p class="price"><sup>€</sup>8</p></div>
  <div class="dish" style="left:853px;top:522px"><p class="dish-name"><span class="initial">L</span>OREM IPSUM</p><p class="dish-desc">Sed ut perspiciatis unde omnis iste natus error sit voluptatem accusantium<span class="leader"></span></p><p class="price"><sup>€</sup>3</p></div>

  <div class="ribbon both" style="left:684px;top:633px">DRINKS</div>

  <div class="dish" style="left:455px;top:708px"><p class="dish-name"><span class="initial">S</span>INT OCCAECAT</p><p class="dish-desc">Sed ut perspiciatis unde omnis iste natus error sit voluptatem accusantium<span class="leader"></span></p><p class="price"><sup>€</sup>5</p></div>
  <div class="dish" style="left:853px;top:708px"><p class="dish-name"><span class="initial">S</span>INT OCCAECAT</p><p class="dish-desc">Sed ut perspiciatis unde omnis iste natus error sit voluptatem accusantium<span class="leader"></span></p><p class="price"><sup>€</sup>5</p></div>
</body>
</html>
```